Report template for evaluation reports to be used by non designers

We are looking for a report template that meets all the requirements listed in the attached documents. letter head, logo etc have been enclosed. Its important that the colour integrity is kept, but beyond that options are welcome.
Its important that the document is extremely easy to use and that is able to be adapted to include eatables, figures, pictures, text boxes etc and keep the integrity of the template

Target Market(s)

Governments, Civil society organisations and research institutions

Font styles to use
Sans Serif

Colors
6b449b
876aae
c0c0c0
000000

Requirements
Must have
• Clean, professional, not concluded, modern, must be easy to use
Should not have
• too busy, hard to use

```html
<!DOCTYPE html>
<html lang="en">
<head>
<meta charset="utf-8">
<title>Evaluation Report Template – Spread</title>
<link href="https://fonts.googleapis.com/css2?family=Open+Sans:wght@400;600;700&display=swap" rel="stylesheet">
<style>
  :root {
    --purple: #6b449b;
    --purple-soft: #876aae;
    --purple-pale: #e6e0f0;
    --grey: #c0c0c0;
    --ink: #000000;
    --text: #333333;
    --paper: #f4f4f4;
    --backdrop: #bdbdbd;
  }
  * { box-sizing: border-box; margin: 0; padding: 0; }
  html, body { width: 1200px; height: 912px; overflow: hidden; }
  body {
    background: var(--backdrop);
    font-family: "Open Sans", Arial, sans-serif;
    color: var(--text);
    position: relative;
  }
  .page {
    position: absolute;
    top: 48px;
    width: 576px;
    height: 816px;
    background: var(--paper);
  }
  .page--left { left: 24px; }
  .page--right { left: 600px; border-left: 1px solid #d2d2d2; }

  /* Left page: chapter divider */
  .chapter-title {
    position: absolute; left: 64px; top: 96px;
    font-size: 28px; font-weight: 700; color: var(--purple);
  }
  .chapter-intro {
    position: absolute; left: 64px; top: 150px; width: 360px;
    border-left: 3px solid var(--purple);
    padding: 2px 0 2px 16px;
    font-size: 11.5px; line-height: 1.5; color: var(--ink);
  }
  .brand {
    font-weight: 600; color: var(--ink); letter-spacing: 0.06em;
    display: flex; align-items: center; gap: 10px;
    white-space: nowrap;
  }
  .brand__dot { width: 12px; height: 12px; border-radius: 50%; background: var(--purple); flex: none; }
  .brand--large { position: absolute; left: 64px; bottom: 80px; font-size: 26px; }
  .brand--small { position: absolute; right: 40px; top: 26px; font-size: 12px; gap: 6px; }
  .brand--small .brand__dot { width: 8px; height: 8px; }

  /* Right page: report content */
  .report-title {
    position: absolute; left: 0; top: 62px; width: 440px; height: 30px;
    border: 2px solid var(--purple-soft); border-left: none;
    border-radius: 0 12px 12px 0;
    padding: 0 0 0 40px;
    display: flex; align-items: center;
    white-space: nowrap;
    font-size: 12.5px; font-weight: 700; color: var(--purple-soft);
  }
  .header-rule {
    position: absolute; left: 440px; top: 62px; width: 136px; height: 0;
    border-top: 2px solid var(--purple-soft);
  }
  .body-text {
    position: absolute; left: 48px; width: 480px;
    font-size: 9.5px; line-height: 1.55; color: var(--ink);
  }
  .body-text--intro { top: 112px; }
  .body-text--after { top: 460px; }

  .data-table {
    position: absolute; left: 48px; top: 200px; width: 480px;
    border-collapse: separate; border-spacing: 2px;
    font-size: 8.5px; color: #444;
  }
  .data-table th {
    background: var(--purple); color: #fff; font-weight: 700;
    padding: 4px 6px; text-align: center;
  }
  .data-table td { padding: 4px 6px; text-align: center; }
  .data-table tr:nth-child(odd) td { background: var(--grey); }
  .data-table tr:nth-child(even) td { background: var(--purple-pale); }
  .data-table td.num { text-align: right; }

  .tick-list { list-style: none; margin-top: 4px; padding-left: 24px; }
  .tick-list li { display: flex; align-items: center; gap: 6px; }
  .tick-list svg { flex: none; }

  .footer-bar {
    position: absolute; left: 48px; right: 40px; bottom: 64px; height: 26px;
    border: 2px solid var(--purple); border-radius: 13px;
    display: flex; align-items: center; justify-content: space-between;
    padding: 0 14px;
    font-size: 8.5px; color: var(--ink);
  }
  .footer-bar b { font-weight: 700; }
  .page-number {
    background: var(--purple); color: #fff; font-weight: 700;
    height: 22px; min-width: 52px; margin-right: -14px;
    border-radius: 11px; display: flex; align-items: center; justify-content: center;
  }
</style>
</head>
<body>

<section class="page page--left">
  <h1 class="chapter-title">Chapter Divider</h1>
  <p class="chapter-intro">
    Lorem ipsum dolor sit amet, consectetur adipiscing elit. Fusce nisl metus, tempus sit amet auctor non, eleifend sit amet metus.
    Cras ante nibh, adipiscing in sodales at, semper at augue. Duis dictum posuere dolor, sed interdum massa laoreet id. Vivamus vehicula accumsan nibh, vel tincidunt nunc porta et. Praesent ligula tortor, luctus at laoreet eget, sagittis lacinia arcu. Duis laoreet nisl eget lectus sodales id mollis augue facilisis.
  </p>
  <div class="brand brand--large"><span class="brand__dot"></span>Northfield Research Institute</div>
</section>

<section class="page page--right">
  <h2 class="report-title">Pre-Study for an Impact Evaluation of the ABC programme</h2>
  <div class="header-rule"></div>
  <div class="brand brand--small"><span class="brand__dot"></span>Northfield Research Institute</div>

  <p class="body-text body-text--intro">
    Lorem ipsum dolor sit amet, consectetur adipiscing elit. Vestibulum vel ante ac ligula vestibulum hendrerit id eu mi. Vestibulum maximus mattis erat. Quisque lacus mi, volutpat vel justo eu, hendrerit blandit nibh. Nunc efficitur tincidunt sapien, in accumsan diam fringilla ut. Nullam molestie mi eget placerat rhoncus. Donec et pharetra enim. Nam fermentum nisl sit amet nulla posuere posuere. Quisque id arcu elementum, efficitur urna vel, tempor est.
  </p>

  <table class="data-table">
    <thead>
      <tr><th>No.</th><th>Lorium</th><th>Art. No.</th><th>haselius tincidunt</th><th>Quisque</th><th>Ipsum</th></tr>
    </thead>
    <tbody>
      <tr><td>1</td><td>1</td><td>2331</td><td>consectetur adipiscing elit.</td><td class="num">7.450,00 €</td><td class="num">7.450,00 €</td></tr>
      <tr><td>2</td><td>0</td><td>5557</td><td>Praesent eleifend tempor velit</td><td class="num">5.490,00 €</td><td class="num">3.290,00 €</td></tr>
      <tr><td>3</td><td>1</td><td>9999</td><td>Quisque vitae tellus nisl</td><td class="num">365,00 €</td><td class="num">365,00 €</td></tr>
      <tr><td>4</td><td>2</td><td>7666</td><td>id tincidunt nunc turpis quis lacus</td><td class="num">6.490,00 €</td><td class="num">390,00 €</td></tr>
      <tr><td>5</td><td>1</td><td>194</td><td>Praesent tincidunt placerat felis</td><td class="num">5.490,00 €</td><td class="num">5.490,00 €</td></tr>
      <tr><td>6</td><td>3</td><td>540</td><td>Pellentesque ut nibh eget nisi cursus ultrices</td><td class="num">5.490,00 €</td><td class="num">5.490,00 €</td></tr>
      <tr><td>7</td><td>3</td><td>1945</td><td>Quisque id ipsum lorem</td><td class="num">5.490,00 €</td><td class="num">5.490,00 €</td></tr>
      <tr><td>8</td><td>2</td><td>5990</td><td>Duis rutrum scelerisque malesuada</td><td></td><td></td></tr>
    </tbody>
  </table>

  <div class="body-text body-text--after">
    <p>Lorem ipsum dolor sit amet, consectetur adipiscing elit. Vestibulum vel ante ac ligula vestibulum hendrerit id eu mi. Vestibulum maximus mattis erat. Quisque lacus mi, volutpat vel justo eu, hendrerit blandit nibh:</p>
    <ul class="tick-list">
      <li><svg width="9" height="9" viewBox="0 0 10 10"><circle cx="5" cy="5" r="4" fill="none" stroke="#6b449b" stroke-width="1.6"/><path d="M3 5.2l1.4 1.4L7 3.8" fill="none" stroke="#6b449b" stroke-width="1.4"/></svg>Vestibulum vel ante ac ligula vestibulum hendrerit id eu mi.</li>
      <li><svg width="9" height="9" viewBox="0 0 10 10"><circle cx="5" cy="5" r="4" fill="none" stroke="#6b449b" stroke-width="1.6"/><path d="M3 5.2l1.4 1.4L7 3.8" fill="none" stroke="#6b449b" stroke-width="1.4"/></svg>Donec et pharetra enim. Nam fermentum nisl sit amet nulla posuere posuere.</li>
      <li><svg width="9" height="9" viewBox="0 0 10 10"><circle cx="5" cy="5" r="4" fill="none" stroke="#6b449b" stroke-width="1.6"/><path d="M3 5.2l1.4 1.4L7 3.8" fill="none" stroke="#6b449b" stroke-width="1.4"/></svg>itae consequat lectus dignissim eget.</li>
    </ul>
  </div>

  <footer class="footer-bar">
    <span><b>Report version:</b> 3</span>
    <span><b>Client:</b> ABC Company</span>
    <span>September 22, 2018</span>
    <span class="page-number">2</span>
  </footer>
</section>

</body>
</html>
```